I need a business card designed using the logo provided either vertical or horizontal......Harbourline Property Group is an Australian based real estate company that caters for the upper end of the market so the design of the business card "must reflect" the companies image!!
Colour combinations are optional but "must be realistic" and must be able to be accurately useable CMYK colours.
Please consider that any colours used "must be able to be used" and be suitable in following designs for "pull out banner signs" and "real estate signs".
The colours and the font in the attached designs are for example and other combinations are encouraged.
Target Market(s)
The High End of the Australian real estate market
Industry/Entity Type
Business
Contact Information for Business Card
Logo - Business Name - Director + Licensed Real Estate Agent - Mobile Number (Cell Phone) - Business Number - Fax - Email Address - Web address
Requirements
Must have
- Designs and colours (CMYK) that can easily be interpreted by an Australian printer.
Nice to have
- Some alternative ideas on colour and font..........the ones provided are ok and have been provided as an example but I am looking for alternative ideas
Should not have
- Loud, overly bright colours. Designs that do not reflect the professional standards of the business.
- Designs that look good on a computer monitor but can not be re-created on a printing press.............this is most important when it comes to shading etc.

```html
<!DOCTYPE html>
<html lang="en">
<head>
<meta charset="utf-8">
<title>Harbourline Property Group – Business Card</title>
<link rel="stylesheet" href="https://fonts.googleapis.com/css2?family=Roboto+Condensed:wght@400;700&display=swap">
<style>
  :root {
    --stage: #e7e4df;
    --card-top: #ffffff;
    --card-bottom: #dcdcdc;
    --gold: #a9782c;
    --gold-soft: #b9a57b;
    --ink: #2b2b2b;
    --ink-strong: #1e1e1e;
    --divider: #8c8c8c;
  }
  * { box-sizing: border-box; margin: 0; padding: 0; }
  html, body {
    width: 1200px; height: 892px; overflow: hidden;
    background: var(--stage);
    font-family: "Roboto Condensed", "Arial Narrow", sans-serif;
  }
  .canvas {
    position: relative; width: 1200px; height: 892px;
    display: flex; align-items: center; justify-content: center;
  }
  .business-card {
    position: relative;
    width: 1000px; height: 572px;
    background: linear-gradient(160deg, var(--card-top) 0%, #f3f3f3 45%, var(--card-bottom) 100%);
    box-shadow: 0 18px 40px rgba(0,0,0,0.22), 0 3px 8px rgba(0,0,0,0.12);
    display: flex;
  }
  .brand-side {
    width: 52%;
    display: flex; align-items: center; justify-content: center;
    padding: 40px;
  }
  .brand-name {
    display: flex; align-items: center; gap: 18px;
    color: var(--ink-strong);
    font-weight: 700;
    font-size: 46px;
    line-height: 1.05;
    text-transform: uppercase;
    letter-spacing: 1px;
  }
  .brand-square {
    width: 30px; height: 30px; flex: none;
    background: var(--gold);
  }
  .divider {
    position: absolute; left: 52%; top: 30px; bottom: 30px; width: 1px;
    background: linear-gradient(to bottom, transparent, var(--divider) 20%, var(--divider) 80%, transparent);
  }
  .contact-side {
    width: 48%;
    padding: 70px 40px 40px 50px;
    display: flex; flex-direction: column;
  }
  .person-name {
    color: var(--gold);
    font-weight: 700;
    font-size: 52px;
    line-height: 1;
  }
  .person-role {
    color: var(--ink);
    font-size: 20px;
    margin-top: 6px;
  }
  .contact-list {
    list-style: none;
    margin-top: 56px;
    display: flex; flex-direction: column; gap: 10px;
  }
  .contact-item {
    display: flex; align-items: flex-start; gap: 18px;
    color: var(--ink);
    font-size: 28px;
    line-height: 1.15;
  }
  .contact-icon { width: 20px; height: 20px; flex: none; margin-top: 8px; fill: var(--gold); }
</style>
</head>
<body>
<main class="canvas">
  <article class="business-card">
    <section class="brand-side">
      <div class="brand-name">
        <span class="brand-square"></span>
        <span>Harbourline<br>Property Group</span>
      </div>
    </section>
    <div class="divider"></div>
    <section class="contact-side">
      <h1 class="person-name">Employee name</h1>
      <p class="person-role">Managing Director</p>
      <ul class="contact-list">
        <li class="contact-item">
          <svg class="contact-icon" viewBox="0 0 24 24" aria-hidden="true"><path d="M6.6 10.8a15.1 15.1 0 0 0 6.6 6.6l2.2-2.2a1 1 0 0 1 1-.25 11.4 11.4 0 0 0 3.6.57 1 1 0 0 1 1 1V20a1 1 0 0 1-1 1A17 17 0 0 1 3 4a1 1 0 0 1 1-1h3.5a1 1 0 0 1 1 1c0 1.25.2 2.45.57 3.57a1 1 0 0 1-.25 1z"/></svg>
          <span>02 8123 4567</span>
        </li>
        <li class="contact-item">
          <svg class="contact-icon" viewBox="0 0 24 24" aria-hidden="true"><path d="M2 5h20v14H2z M3 6l9 7 9-7" stroke="#fff" stroke-width="1.5"/></svg>
          <span>info@harbourlinegroup.com</span>
        </li>
        <li class="contact-item">
          <svg class="contact-icon" viewBox="0 0 24 24" aria-hidden="true"><circle cx="12" cy="12" r="10"/><path d="M2 12h20M12 2c3 3 3 17 0 20M12 2c-3 3-3 17 0 20" stroke="#fff" stroke-width="1.3" fill="none"/></svg>
          <span>www.harbourlinegroup.com</span>
        </li>
        <li class="contact-item">
          <span class="contact-icon"></span>
          <span>14 Quayside Lane<br>Harbour Point, NSW 2000</span>
        </li>
      </ul>
    </section>
  </article>
</main>
</body>
</html>
```